Complete Website Redesign

We need a complete revamp of our website. Need to add interactive custmer catalog seection tools. Need to add customer spec input for recommended product search results. Need a cutomer lead and opportunity contact capability. Need a complete Branding message revamp. Primary visuals will be prodcut pictures and case studies.
Target Market(s)
Industrial Customers in the high durability Air movement and fan/blower space; high durability enclosure and flow industries ie. mining, chamicals, manufacturing, water treatment, chemical in use manufacturing
Look and feel
Each slider illustrates characteristics of the customer's brand and the style your logo design should communicate.

```html
<!DOCTYPE html>
<html lang="en">
<head>
<meta charset="utf-8">
<title>DCX – Duraform Composite Works, LLC</title>
<link href="https://fonts.googleapis.com/css2?family=Source+Sans+3:wght@400;600;700&family=Marcellus&display=swap" rel="stylesheet">
<style>
:root{
  --navy:#1f2f8f;
  --ink:#333;
  --rule:#dddddd;
  --wine:#5a1010;
  --alert:#e01b1b;
  --red-tab:#a50d12;
  --sage:#7f9c95;
  --footer:#2a2628;
  --footer-deep:#1e1c1d;
  --panel:#1b181a;
  --field:#3a3638;
  --reset:#3e6db0;
}
*{box-sizing:border-box;margin:0;padding:0}
html,body{width:1200px;height:1000px;overflow:hidden;background:#fff}
body{position:relative;font-family:"Source Sans 3",sans-serif;color:var(--ink)}
.abs{position:absolute}
.top-bar{left:0;top:0;width:1200px;height:5px;background:var(--navy)}
.brand{left:56px;top:20px;display:flex;align-items:center;gap:10px}
.brand-mark{width:40px;height:40px;background:var(--navy)}
.brand-name{font-size:38px;font-weight:600;color:var(--navy);line-height:1}
.brand-sub{left:56px;top:66px;font-size:15px;font-weight:600;color:var(--navy)}
.main-nav{top:66px;font-size:12.5px;letter-spacing:.4px;color:var(--ink)}
.header-rule{left:35px;top:94px;width:1117px;height:1px;background:var(--rule)}
.hero{left:40px;top:103px;width:1106px;height:322px;background:linear-gradient(#f6f6f6,#e3e3e3)}
.hero-photo{left:100px;top:12px;width:920px;height:220px;background:linear-gradient(180deg,#d8dae2,#eceef2)}
.hero-line{left:0;width:1106px;text-align:center;font-family:"Marcellus",serif;font-size:18.5px;letter-spacing:.4px;color:#333}
.selector{left:78px;top:425px;width:1025px;height:68px;border:1px solid #cfcfcf;border-top:none;background:#f8f8f8}
.selector-label{left:182px;top:10px;font-size:20px;color:var(--wine)}
.selector-input{left:348px;top:9px;width:425px;height:27px;background:#ececec;border:1px solid #ddd}
.selector-btn{left:784px;top:12px;width:76px;height:23px;border-radius:5px;background:var(--sage);color:#fff;font-size:13px;font-weight:600;text-align:center;line-height:23px}
.selector-hint{left:0;top:45px;width:1123px;text-align:center;font-size:12px;color:var(--alert)}
.section-rule{top:536px;height:1px;background:var(--rule)}
.section-title{left:0;width:1166px;top:526px;text-align:center;font-size:15.5px;letter-spacing:.6px;color:#222}
.card{top:577px;width:165px;height:212px;border:1px solid #d2d2d2;background:#fff}
.card-photo{left:16px;top:42px;width:132px;height:140px;background:linear-gradient(#e6e8ee,#c7cad3)}
.card-label{top:581px;height:30px;background:var(--navy);color:#fff;font-size:14.5px;font-weight:600;text-align:center;line-height:29px}
.more-tab{right:-1px;bottom:-1px}
.footer{left:0;top:817px;width:1200px;height:140px;background:var(--footer)}
.footer-bottom{left:0;top:957px;width:1200px;height:43px;background:var(--footer-deep);color:#bdbdbd;font-size:14.5px;text-align:center;line-height:52px}
.footer-head{top:826px;color:#fff;font-size:14px;font-weight:600;letter-spacing:.4px;text-align:center;width:160px}
.quote{left:74px;top:849px;width:196px;height:80px;background:#111;border-radius:10px;padding:8px 10px;font-size:10px;line-height:12.8px;color:#fff;font-weight:600}
.quote em{font-style:normal;color:var(--alert)}
.quote-author{left:210px;top:938px;font-size:11.5px;color:#ddd}
.social{width:31px;height:31px;border-radius:6px;background:#6b6669}
.form-panel{top:849px;height:108px;background:var(--panel);border-radius:6px 6px 0 0}
.field{background:var(--field);color:#9a9698;font-size:12px;padding:2px 8px;height:20px}
.btn{height:17px;color:#fff;font-size:12px;font-weight:600;text-align:center;line-height:17px}
.btn-red{background:#9b0a0a}
.btn-blue{background:var(--reset)}
</style>
</head>
<body>
<div class="abs top-bar"></div>
<div class="abs brand"><div class="brand-mark"></div><span class="brand-name">DCX</span></div>
<div class="abs brand-sub">Duraform Composite Works, LLC</div>
<nav>
  <span class="abs main-nav" style="left:534px">HOME</span>
  <span class="abs main-nav" style="left:610px">PRODUCTS &nbsp;&nbsp;↓</span>
  <span class="abs main-nav" style="left:712px">ABOUT US</span>
  <span class="abs main-nav" style="left:809px">MISSION</span>
  <span class="abs main-nav" style="left:896px">REQUEST INFORMATION</span>
  <span class="abs main-nav" style="left:1065px">CONTACTS</span>
</nav>
<div class="abs header-rule"></div>

<section class="abs hero">
  <div class="abs hero-photo" role="img" aria-label="Product photo lineup: axial fan, centrifugal blower, high plume exhaust fans and louvered roof ventilator"></div>
  <p class="abs hero-line" style="top:262px">WE HAVE A WIDE SELECION OF FIBERGLASS FANS AND OTHER CORROSION RESISTANT AIR HANDLING</p>
  <p class="abs hero-line" style="top:287px">SOLUTIONS FOR OEMS, CONTRACTORS AND PLANT MAINTENANCE OPERATIONS.</p>
</section>

<section class="abs selector">
  <span class="abs selector-label">Product Selection</span>
  <div class="abs selector-input"></div>
  <div class="abs selector-btn">Submit</div>
  <p class="abs selector-hint">To verify a catalog number and access product information, enter the complete number (including dashes) above.</p>
</section>

<div class="abs section-rule" style="left:40px;width:472px"></div>
<div class="abs section-rule" style="left:653px;width:498px"></div>
<h2 class="abs section-title" style="font-weight:400;left:17px">OUR PRODUCTS</h2>

<div class="abs card" style="left:54px"><div class="abs card-photo" role="img" aria-label="Fiberglass centrifugal fan photo"></div><svg class="abs more-tab" width="80" height="21"><polygon points="20,0 80,0 80,21 0,21" fill="#a50d12"/><text x="24" y="15" fill="#fff" font-family="Source Sans 3,sans-serif" font-size="12" font-weight="700">more &gt;&gt;</text></svg></div>
<div class="abs card" style="left:281px"><div class="abs card-photo" role="img" aria-label="High plume exhaust fans photo"></div><svg class="abs more-tab" width="80" height="21"><polygon points="20,0 80,0 80,21 0,21" fill="#a50d12"/><text x="24" y="15" fill="#fff" font-family="Source Sans 3,sans-serif" font-size="12" font-weight="700">more &gt;&gt;</text></svg></div>
<div class="abs card" style="left:515px"><div class="abs card-photo" role="img" aria-label="Fiberglass louver and damper photo"></div><svg class="abs more-tab" width="80" height="21"><polygon points="20,0 80,0 80,21 0,21" fill="#a50d12"/><text x="24" y="15" fill="#fff" font-family="Source Sans 3,sans-serif" font-size="12" font-weight="700">more &gt;&gt;</text></svg></div>
<div class="abs card" style="left:741px"><div class="abs card-photo" role="img" aria-label="Fiberglass axial propeller photo"></div><svg class="abs more-tab" width="80" height="21"><polygon points="20,0 80,0 80,21 0,21" fill="#a50d12"/><text x="24" y="15" fill="#fff" font-family="Source Sans 3,sans-serif" font-size="12" font-weight="700">more &gt;&gt;</text></svg></div>
<div class="abs card" style="left:967px"><div class="abs card-photo" role="img" aria-label="Fiberglass axial fan photo"></div><svg class="abs more-tab" width="80" height="21"><polygon points="20,0 80,0 80,21 0,21" fill="#a50d12"/><text x="24" y="15" fill="#fff" font-family="Source Sans 3,sans-serif" font-size="12" font-weight="700">more &gt;&gt;</text></svg></div>

<div class="abs card-label" style="left:42px;width:190px">Fiberglass Centrifugal Fans</div>
<div class="abs card-label" style="left:270px;width:188px">High Plume Exhaust Fans</div>
<div class="abs card-label" style="left:504px;width:188px;font-size:13.5px">Fiberglass Louvers &amp; Dampers</div>
<div class="abs card-label" style="left:731px;width:188px">Fiberglass axial Propellers</div>
<div class="abs card-label" style="left:957px;width:189px">Fiberglass Axial Fans</div>

<footer>
  <div class="abs footer"></div>
  <h3 class="abs footer-head" style="left:84px">TESTIMONIALS</h3>
  <h3 class="abs footer-head" style="left:334px">FOLLOW US</h3>
  <h3 class="abs footer-head" style="left:597px">NEWSLETTER</h3>

  <blockquote class="abs quote">I have been very satisfied with all of the service provided by <em>DCX</em>. All of your personnel are really focused and were so courteous and professional acting.</blockquote>
  <svg class="abs" style="left:150px;top:928px" width="56" height="24"><polygon points="0,0 56,0 50,22" fill="#111"/></svg>
  <span class="abs quote-author">Mr. Doe</span>

  <div class="abs social" style="left:342px;top:855px"></div>
  <div class="abs social" style="left:380px;top:855px"></div>
  <div class="abs social" style="left:417px;top:855px"></div>
  <div class="abs social" style="left:454px;top:855px"></div>
  <div class="abs social" style="left:342px;top:898px"></div>
  <div class="abs social" style="left:380px;top:898px"></div>
  <div class="abs social" style="left:418px;top:898px"></div>

  <div class="abs form-panel" style="left:564px;width:236px"></div>
  <div class="abs field" style="left:587px;top:861px;width:194px">Your Name</div>
  <div class="abs field" style="left:587px;top:889px;width:194px">Your Email</div>
  <div class="abs btn btn-red" style="left:727px;top:934px;width:53px">Submit</div>

  <div class="abs form-panel" style="left:858px;width:236px"></div>
  <div class="abs field" style="left:876px;top:861px;width:194px">Your Email</div>
  <div class="abs field" style="left:876px;top:889px;width:195px;height:40px">Your Message</div>
  <div class="abs btn btn-blue" style="left:957px;top:934px;width:52px">Reset</div>
  <div class="abs btn btn-red" style="left:1017px;top:934px;width:53px">Submit</div>

  <div class="abs footer-bottom">Copyright ©&nbsp; DCX&nbsp; 2013. All rights reserved.</div>
</footer>
</body>
</html>
```